Verodex business card

Business card for sustainable investment company called "Verodex". Verodex is an exchange platform selling carbon credits between buyers and sellers. Carbon Credits are an environmental commodity for reducing global carbon emissions.

the card should obviously have our logo and the theme should be sustainability/environment mixed with a trading platform.

Contact Information for Business Card

Logo, Name, Title, Phone, Email

Colors
0054AA
0677BA
7BADD7
CADEEF
E8F1F8
0094D4
00A9DD
6FCCEA
C7EBF8
E9F6FB
00AB8E
00BBA5
67D7C9
C6EFE9
E9F9F6
59FF00
82FF00
B8FF75
E3FFCB
F4FFEA

```html
<!DOCTYPE html>
<html lang="en">
<head>
<meta charset="utf-8">
<title>Verodex business card</title>
<link rel="stylesheet" href="https://fonts.googleapis.com/css2?family=Montserrat:wght@400;500;600;700&display=swap">
<style>
  :root {
    --backdrop: #e8e9eb;
    --navy: #172a50;
    --white: #ffffff;
    --sky: #2fb6e8;
    --sky-light: #67cbe6;
    --blue: #3f7fc9;
    --ink: #1d1d1f;
  }
  * { margin: 0; padding: 0; box-sizing: border-box; }
  html, body {
    width: 1200px; height: 900px; overflow: hidden;
    background: var(--backdrop);
    font-family: "Montserrat", sans-serif;
  }
  .canvas { position: relative; width: 1200px; height: 900px; }
  .card {
    position: absolute; left: 300px; width: 600px; height: 343px;
    overflow: hidden; box-shadow: 0 6px 18px rgba(0,0,0,0.12);
  }
  .card-front { top: 85px; background: var(--navy); }
  .card-back { top: 472px; background: var(--white); }

  .brand { position: absolute; display: flex; align-items: center; gap: 18px; }
  .brand-dot {
    width: 46px; height: 46px; border-radius: 50%;
    background: linear-gradient(135deg, var(--sky-light), var(--blue));
  }
  .brand-name { font-weight: 600; letter-spacing: 2px; line-height: 1; }
  .card-front .brand { left: 50%; top: 50%; transform: translate(-50%, -50%); }
  .card-front .brand-name { color: var(--white); font-size: 58px; }

  .card-back .brand { left: 50%; top: 62px; transform: translateX(-50%); }
  .card-back .brand-dot { width: 40px; height: 40px; }
  .card-back .brand-name { color: var(--navy); font-size: 50px; }

  .details {
    position: absolute; left: 0; right: 0; top: 150px;
    display: flex; justify-content: center; align-items: center; gap: 16px;
  }
  .person { text-align: right; }
  .person-name { font-weight: 700; font-size: 21px; letter-spacing: 0.5px; }
  .person-name .first { color: var(--sky); }
  .person-name .last { color: var(--navy); }
  .person-title { font-size: 15px; color: var(--ink); margin-top: 2px; }
  .divider { width: 1.5px; height: 64px; background: var(--sky); }
  .contacts { list-style: none; font-size: 13.5px; color: var(--ink); }
  .contacts li { display: flex; align-items: center; gap: 8px; line-height: 21px; }
  .contacts svg { width: 14px; height: 14px; flex: none; }

  .band { position: absolute; left: 0; bottom: 0; width: 600px; height: 70px; }
</style>
</head>
<body>
<main class="canvas">
  <section class="card card-front" aria-label="Card front">
    <div class="brand">
      <span class="brand-dot"></span>
      <span class="brand-name">VERODEX</span>
    </div>
  </section>

  <section class="card card-back" aria-label="Card back">
    <div class="brand">
      <span class="brand-dot"></span>
      <span class="brand-name">VERODEX</span>
    </div>

    <div class="details">
      <div class="person">
        <p class="person-name"><span class="first">DANIEL</span> <span class="last">MAREK</span></p>
        <p class="person-title">Co-Founder</p>
      </div>
      <span class="divider"></span>
      <ul class="contacts">
        <li>
          <svg viewBox="0 0 16 16"><path fill="#2fb6e8" d="M3.5 1.5l2.5 0 1 3.5-1.8 1.2a8 8 0 0 0 4.6 4.6L11 9l3.5 1v2.5c0 1-.8 1.8-1.8 1.8C6.9 14.3 1.7 9.1 1.7 3.3c0-1 .8-1.8 1.8-1.8z"/></svg>
          555-204-3187
        </li>
        <li>
          <svg viewBox="0 0 16 16"><rect x="1" y="3" width="14" height="10" rx="1" fill="#3f7fc9"/><path d="M1.5 3.8L8 9l6.5-5.2" fill="none" stroke="#fff" stroke-width="1.2"/></svg>
          info@verodex.com
        </li>
        <li>
          <svg viewBox="0 0 16 16"><circle cx="8" cy="8" r="7" fill="#2fb6e8"/><path d="M1 8h14M8 1c-3 3.5-3 10.5 0 14M8 1c3 3.5 3 10.5 0 14" fill="none" stroke="#fff" stroke-width="1"/></svg>
          www.verodex.com
        </li>
      </ul>
    </div>

    <svg class="band" viewBox="0 0 600 70" aria-hidden="true">
      <defs>
        <linearGradient id="stripe" x1="0" y1="0" x2="1" y2="0">
          <stop offset="0" stop-color="#67cbe6"/>
          <stop offset="0.5" stop-color="#2fb6e8"/>
          <stop offset="1" stop-color="#3f7fc9"/>
        </linearGradient>
      </defs>
      <rect x="0" y="50" width="430" height="20" fill="url(#stripe)"/>
      <polygon points="436,24 600,0 600,70 436,70" fill="#172a50"/>
    </svg>
  </section>
</main>
</body>
</html>
```